Security based company delivering Ironpath Tactical Training Agencies Worldwide.

We need a Web design for a company doing business in Washington D.C. We deliver Ironpath Tactical Training Agencies throughout the world. Our focus is on Improvised Explosive Devices. We train Bomb Technicians and First Responders in all aspects relating to bombings and criminal incidents globally.
Updates

Reason: We have uploaded our logo. Thank you.

Target Market(s)

Military and Law Enforcement Personnel from around the world.

Industry/Entity Type

Business

Requirements
Should not have
• Do not include cartoon like characters.

```html
<!DOCTYPE html>
<html lang="en">
<head>
<meta charset="utf-8">
<title>Ironpath Tactical Training Agencies</title>
<link href="https://fonts.googleapis.com/css2?family=Open+Sans:ital,wght@0,400;0,600;0,700;1,400;1,600&display=swap" rel="stylesheet">
<style>
:root{
  --blue:#5b93d3;
  --blue-dark:#4a80c0;
  --blue-light:#7aaee6;
  --ink:#1a1a1a;
  --topbar:#efefef;
  --panel:#e4e4e4;
  --footer:#3b3b3b;
  --footer-base:#121212;
  --white:#ffffff;
}
*{box-sizing:border-box;margin:0;padding:0}
html,body{width:961px;height:1200px;overflow:hidden}
body{font-family:"Open Sans",Arial,sans-serif;color:var(--ink);background:var(--white);position:relative}
.abs{position:absolute}

.topbar{left:0;top:0;width:961px;height:29px;background:var(--topbar);border-bottom:1px solid #bdbdbd}
.topbar .phone{left:104px;top:7px;font-size:11px;display:flex;align-items:center;gap:5px}
.topbar .follow{right:105px;top:4px;font-size:11px;display:flex;align-items:center;gap:4px}
.dot-icon{width:20px;height:20px;border-radius:50%;background:radial-gradient(circle at 35% 30%,#9cc4ee,#6a9fdc);box-shadow:inset 0 0 0 1px rgba(255,255,255,.35);display:inline-block}

.header{left:0;top:29px;width:961px;height:111px}
.brand-mark{left:109px;top:8px;width:92px;height:92px;border-radius:50%;background:var(--blue-light)}
.brand-line1{left:218px;top:26px;font-size:20px;font-weight:700;letter-spacing:3.4px;color:var(--blue-light)}
.brand-line2{left:218px;top:54px;font-size:19.5px;font-weight:600;color:#111}
.register{left:777px;top:24px;font-size:11.5px;font-weight:600}
.search{left:743px;top:59px;width:114px;height:27px;border:1px solid #b9b9b9;border-radius:3px;background:#f6f6f6;font-size:10px;color:#9a9a9a;padding:7px 7px;display:flex;justify-content:space-between;align-items:center}

.nav{left:0;top:140px;width:961px;height:35px;background:linear-gradient(#6aa0dc,#4f88c9)}
.nav ul{list-style:none;display:flex;position:absolute;left:110px;top:8px}
.nav li{color:var(--white);font-size:13px;margin-right:42px}
.nav li:last-child{margin-right:0}

.hero{left:0;top:175px;width:961px;height:344px;background:linear-gradient(105deg,#3f4a2e 0%,#5d6a42 14%,#7f855f 24%,#b8ad92 36%,#d6ccb8 50%,#e3ddd2 64%,#d9d2c4 78%,#c8bca6 90%,#b5a78e 100%)}
.hero-caption{left:280px;top:34px;width:432px;height:157px;border:6px solid #6b9ad2;border-radius:6px;background:rgba(70,68,64,.92);color:var(--white);font-size:29px;line-height:41px;text-align:center;padding-top:14px}
.hero-arrow{top:145px;width:34px;height:34px;background:rgba(90,90,90,.75);display:flex;align-items:center;justify-content:center}
.hero-dots{left:457px;top:322px;display:flex;gap:7px}
.hero-dots span{width:11px;height:11px;border:1.5px solid #222;background:var(--blue)}
.hero-dots span.on{background:#fff}

.card{top:547px;width:240px;height:144px;border:2px solid var(--blue)}
.card .pic{height:107px}
.card .label{text-align:center;font-size:14.5px;font-weight:600;padding-top:8px}

.panel{top:719px;width:371px;height:180px;background:var(--panel);text-align:center}
.panel h2{font-size:14px;font-weight:600;margin-top:4px}
.panel p{font-size:9.3px;line-height:14px;margin:8px 14px 0}
.btn{display:inline-block;background:#000;color:#fff;font-size:12px;font-weight:600;padding:5px 9px;border-radius:3px}

.footer{left:0;top:927px;width:961px;height:243px;background:var(--footer);color:var(--white)}
.footer h3{font-size:15px;font-weight:700;position:absolute;top:26px}
.foot-text{font-size:10px;line-height:14.5px}
.links{list-style:none;font-size:10px}
.links li{height:16.4px;display:flex;align-items:center;gap:10px}
.fb-box{left:491px;top:62px;width:176px;height:154px;background:#fff;border-radius:3px;color:var(--ink)}
.email-input{left:693px;top:80px;width:162px;height:30px;background:#fff;border-radius:3px}
.send{left:747px;top:118px;background:#000;color:#fff;font-size:12px;font-weight:600;padding:4px 11px;border-radius:3px}
.social-row{left:701px;top:153px;display:flex;gap:4px}
.social-row span{width:35px;height:35px;border-radius:50%;background:radial-gradient(circle at 35% 30%,#a3c9f0,#6599d6);box-shadow:inset 0 0 0 2px rgba(255,255,255,.25)}

.base{left:0;top:1170px;width:961px;height:30px;background:var(--footer-base);color:#e8e8e8;font-size:10.5px;text-align:center;line-height:30px}
</style>
</head>
<body>

<div class="abs topbar">
  <div class="abs phone">
    <svg width="9" height="9" viewBox="0 0 10 10"><path d="M2 0.5 L3.6 0.5 L4.2 3 L3 3.8 Q4 6 6.2 7 L7 5.8 L9.5 6.4 L9.5 8 Q9.5 9.5 8 9.5 Q0.5 9 0.5 2 Q0.5 0.5 2 0.5Z" fill="#222"/></svg>
    1800-3914-2270
  </div>
  <div class="abs follow" aria-label="Social network links">
    <span style="margin-right:3px">Follow Us :</span>
    <span class="dot-icon"></span><span class="dot-icon"></span><span class="dot-icon"></span><span class="dot-icon"></span><span class="dot-icon"></span>
  </div>
</div>

<header class="abs header">
  <div class="abs brand-mark"></div>
  <div class="abs brand-line1">IRONPATH TACTICAL TRAINING</div>
  <div class="abs brand-line2">AGENCIES</div>
  <div class="abs register">Ragister Now</div>
  <div class="abs search">
    <span>Search</span>
    <svg width="10" height="10" viewBox="0 0 10 10"><circle cx="4" cy="4" r="3" fill="none" stroke="#111" stroke-width="1.6"/><line x1="6.2" y1="6.2" x2="9.2" y2="9.2" stroke="#111" stroke-width="1.8"/></svg>
  </div>
</header>

<nav class="abs nav">
  <ul>
    <li>Home</li><li>About Us</li><li>IED Training</li><li>Equipments</li><li>Solutions</li><li>Resources</li><li>News</li><li>Contact Us</li>
  </ul>
</nav>

<section class="abs hero" role="img" aria-label="Bomb technician in a green protective suit kneeling beside equipment on sandy ground near a pale block wall">
  <div class="abs hero-caption">Successfully Delivering<br>Tactical, Operational<br>And Strategic Capabilites</div>
  <div class="abs hero-arrow" style="left:4px">
    <svg width="14" height="12" viewBox="0 0 14 12"><path d="M6 1 L1 6 L6 11 M12 1 L7 6 L12 11" fill="none" stroke="#fff" stroke-width="1.4"/></svg>
  </div>
  <div class="abs hero-arrow" style="left:918px">
    <svg width="14" height="12" viewBox="0 0 14 12"><path d="M2 1 L7 6 L2 11 M8 1 L13 6 L8 11" fill="none" stroke="#fff" stroke-width="1.4"/></svg>
  </div>
  <div class="abs hero-dots"><span></span><span class="on"></span><span></span></div>
</section>

<div class="abs card" style="left:100px">
  <div class="pic" role="img" aria-label="Silhouettes of soldiers on a ridge against an orange sunset" style="background:linear-gradient(#f6c22a 0%,#f0a41c 55%,#c8760f 78%,#2a1c08 100%)"></div>
  <div class="label">Explosive Mangment</div>
</div>
<div class="abs card" style="left:361px">
  <div class="pic" role="img" aria-label="Reading glasses resting on an open book" style="background:linear-gradient(160deg,#f8d27a 0%,#f0ae4a 45%,#e08a2e 75%,#b85e18 100%)"></div>
  <div class="label">Learning</div>
</div>
<div class="abs card" style="left:622px">
  <div class="pic" role="img" aria-label="Close-up of an electronic circuit board in warm light" style="background:linear-gradient(135deg,#7a2808 0%,#c4560e 35%,#f0a020 55%,#b44a0c 75%,#4a1404 100%)"></div>
  <div class="label">Solutions</div>
</div>

<section class="abs panel" style="left:100px">
  <h2>Testimonial</h2>
  <p>ITS has the incredible ability to combine tactical and strategic capabilities to bring a programme together for successful delivery. The ITS team is extremely focused, brilliant under pressure and inspiring.</p>
  <div class="abs" role="img" aria-label="Portrait of the quoted officer" style="left:64px;top:83px;width:47px;height:47px;border:2px solid var(--blue);background:linear-gradient(90deg,#8a3a3a 0%,#3c4a6a 45%,#2e3a50 70%,#8a7a4a 100%)"></div>
  <div class="abs" style="left:130px;top:89px;text-align:left;font-size:9.5px;line-height:18px">
    <em style="font-weight:600">- Sgt. Maj. Daniel R. Whitcombe</em><br><strong>Daniel</strong>
  </div>
  <div class="abs" style="left:0;width:371px;top:144px"><span class="btn">SEE MORE</span></div>
</section>

<section class="abs panel" style="left:491px">
  <h2>Traning &amp; Learning Solutions</h2>
  <p>Ironpath Tactical Solutions offers bespoke training and solutions with unique expertise in the areas of defence, security and post-conflict recovery. We are proud to be a RK Honours 2011 Winner.</p>
  <p style="margin-top:13px">Other specialities include business improvement, learning and development, logistics and procurement, counter threat and counter improvised explosive devices (C-IEDs).</p>
  <div class="abs" style="left:0;width:371px;top:144px"><span class="btn">READ MORE</span></div>
</section>

<footer class="abs footer">
  <h3 style="left:106px">TRANING CENTER</h3>
  <div class="abs foot-text" style="left:106px;top:62px">
    <div style="display:flex;gap:5px"><svg width="7" height="10" viewBox="0 0 7 10" style="margin-top:2px"><path d="M3.5 0 A3.5 3.5 0 0 1 7 3.5 Q7 6 3.5 10 Q0 6 0 3.5 A3.5 3.5 0 0 1 3.5 0Z" fill="#fff"/><circle cx="3.5" cy="3.5" r="1.3" fill="#3b3b3b"/></svg>
      <span>12 Corvel Row, Marston<br>Avenue Halden, Washington<br>77418</span></div>
    <div style="margin-top:14px;display:flex;gap:6px;align-items:center"><svg width="9" height="9" viewBox="0 0 10 10"><path d="M2 0.5 L3.6 0.5 L4.2 3 L3 3.8 Q4 6 6.2 7 L7 5.8 L9.5 6.4 L9.5 8 Q9.5 9.5 8 9.5 Q0.5 9 0.5 2 Q0.5 0.5 2 0.5Z" fill="#fff"/></svg>1800-3914-2270</div>
    <div style="margin-top:14px;display:flex;gap:6px;align-items:center"><svg width="10" height="8" viewBox="0 0 10 8"><rect width="10" height="8" fill="#fff"/><path d="M0 0 L5 4.5 L10 0" fill="none" stroke="#3b3b3b" stroke-width="1"/></svg>help@ironpathtraining.example</div>
    <div style="margin-top:14px;display:flex;gap:6px;align-items:center"><svg width="9" height="9" viewBox="0 0 10 10"><circle cx="5" cy="5" r="4.5" fill="#fff"/><path d="M0.5 5 H9.5 M5 0.5 Q2 5 5 9.5 Q8 5 5 0.5" fill="none" stroke="#3b3b3b" stroke-width="0.8"/></svg>www.ironpathtraining.example</div>
  </div>

  <h3 style="left:301px">FAST LINKS</h3>
  <ul class="abs links" style="left:308px;top:62px">
    <li><span>&raquo;</span>Home</li><li><span>&raquo;</span>About Us</li><li><span>&raquo;</span>IED Training</li><li><span>&raquo;</span>Equipments</li><li><span>&raquo;</span>Solutions</li><li><span>&raquo;</span>Resources</li><li><span>&raquo;</span>News</li><li><span>&raquo;</span>Contact Us</li>
  </ul>

  <h3 style="left:498px">JOIN OUR COMMUNITY</h3>
  <div class="abs fb-box">
    <div class="abs" style="left:8px;top:5px;width:30px;height:30px;border-radius:50%;background:var(--blue-light)"></div>
    <div class="abs" style="left:53px;top:3px;font-size:11.5px;font-weight:700;color:#2a4d7a;line-height:16px">Ironpath<br>Training</div>
    <div class="abs" style="left:137px;top:20px;width:34px;height:14px;background:#4a6ea8;color:#fff;font-size:8px;text-align:center;line-height:14px;border-radius:2px">Like</div>
    <div class="abs" style="left:6px;top:38px;width:164px;border-top:1px solid #ccc"></div>
    <div class="abs" style="left:7px;top:41px;font-size:8px;color:#2a4d7a">210,413 People Like</div>
    <div class="abs" role="img" aria-label="Grid of member profile pictures" style="left:7px;top:56px;width:164px;height:76px;display:grid;grid-template-columns:repeat(4,1fr);gap:3px">
      <span style="background:linear-gradient(#b8b090,#6a6450)"></span><span style="background:linear-gradient(#8a6ab0,#4e3670)"></span><span style="background:linear-gradient(#8a7a6a,#3a3430)"></span><span style="background:linear-gradient(#5a6f98,#2a3858)"></span>
      <span style="background:linear-gradient(#a05a48,#5a2a22)"></span><span style="background:linear-gradient(#c4b09a,#7a6858)"></span><span style="background:linear-gradient(#6a8a4a,#34502a)"></span><span style="background:linear-gradient(#9a9488,#4e4a42)"></span>
    </div>
    <div class="abs" style="left:6px;top:134px;width:164px;border-top:1px solid #ccc"></div>
    <div class="abs" style="left:7px;top:139px;font-size:8px;color:#2a4d7a;display:flex;gap:5px;align-items:center"><span style="width:8px;height:8px;background:#4a6ea8;display:inline-block"></span>Community page widget</div>
  </div>

  <h3 style="left:693px">NEWS LATTER</h3>
  <div class="abs" style="left:693px;top:61px;font-size:10.5px">Enter Your Email Address</div>
  <div class="abs email-input"></div>
  <div class="abs send">SEND</div>
  <div class="abs social-row" aria-label="Social network links"><span></span><span></span><span></span><span></span></div>
</footer>

<div class="abs base">Ironpath Tactical Training Agencies &copy; 2014</div>

</body>
</html>
```